Kestrel Baseball & Softball Camp 2017

Design a flyer that will promote our 2017 summer camp for boys and girls softball.

Weeks of
July 10th - 14th
July 17th - 21st.

Players ages 5 - 11.
Full day = 9:30am - 2:30pm half day = 9:30am - 11:30am.
$295 / full day : $195/ half day

Hosted by "Kestrel Baseball" affiliated with the Harbor Comets Travel Baseball & Softball Club and the Maple Ridge Youth League,

Camp Location MRYL, Route 9C Birch Hollow.

PHone 555-240-7813, email info@kestrelball.example

The color should be "Red white and blue color scheme" with dates and location standing out. Kestrel Logo should be prominent MRYL and Comets smaller and secondary.

Feel free to use stock photo's if available. visit www.harborcomets.example for more pictures and there are links for the 2017 summer camp there with possibly some more information.

Target Market(s)

to catch the eye of parents of players ages 5 - 11 already at little league or shopping in local stores

Colors
ec1f27
0355a3
ffffff

Requirements
Must have
• red white and blue design,
• Kestrel logo and summer camp prominent so it catches the eye and explains what it is right away.
• the comets and maple ridge logo's a the bottom showing the affiliation.
Nice to have
• stock photo's or something showing players having a great time or a beautiful ballpark
Should not have
• to much clutter or hard to figure out what it's for

```html
<!DOCTYPE html>
<html lang="en">
<head>
<meta charset="utf-8">
<title>Kestrel Softball Summer Camp 2017</title>
<link rel="stylesheet" href="https://fonts.googleapis.com/css2?family=Bebas+Neue&family=Oswald:wght@500&family=Pacifico&display=swap">
<style>
:root{
  --red:#d6232b;
  --navy:#1f3864;
  --grey:#d0d2d5;
  --white:#ffffff;
  --ink:#222222;
  --rule:#9a9a9a;
}
*{margin:0;padding:0;box-sizing:border-box}
html,body{width:817px;height:1200px;overflow:hidden;background:var(--white)}
.flyer{position:relative;width:817px;height:1200px;overflow:hidden;background:var(--white);font-family:"Bebas Neue",sans-serif}
.hero-photo{position:absolute;left:0;top:0;width:817px;height:610px;
  background:linear-gradient(180deg,#b9c4c4 0%,#9aa49a 28%,#8b7a5e 48%,#b98d5c 70%,#6a4a30 100%)}
.grey-panel{position:absolute;left:0;top:0;width:817px;height:820px}
.logo-badge{position:absolute;left:83px;top:82px;width:200px;height:200px;border-radius:50%;background:var(--white);
  display:flex;flex-direction:column;align-items:center;justify-content:center;box-shadow:0 2px 8px rgba(0,0,0,.25)}
.logo-name{font-family:"Bebas Neue",sans-serif;color:var(--red);font-size:58px;line-height:1;letter-spacing:1px}
.script{font-family:"Pacifico",cursive}
.softball{position:absolute;left:92px;top:300px;color:var(--white);font-size:58px;line-height:1}
.headline{position:absolute;left:40px;top:385px;font-size:146px;line-height:1;letter-spacing:1px;white-space:nowrap}
.headline .summer{color:var(--red)}
.headline .camp{color:var(--white)}
.year{position:absolute;left:700px;top:440px;width:110px;transform:rotate(90deg);transform-origin:left top;
  left:767px;top:400px;color:var(--white);font-size:56px;line-height:1}
.audience{position:absolute;left:490px;top:512px;color:var(--white);font-size:16px}
.dash-top{position:absolute;left:40px;top:563px;width:635px;border-top:2px dashed var(--white)}
.weeks{position:absolute;left:78px;top:612px;color:var(--navy);font-size:39px;line-height:1.32;letter-spacing:1px}
.ages{position:absolute;left:432px;top:658px;display:flex;align-items:center;gap:14px}
.ages-label{color:var(--navy);font-size:36px;line-height:1.2;letter-spacing:1px}
.ages-circle{position:absolute;left:610px;top:620px;width:138px;height:138px;border-radius:50%;background:var(--navy);
  color:var(--white);display:flex;align-items:center;justify-content:center;font-size:44px;letter-spacing:1px}
.hours{position:absolute;left:62px;top:834px;display:flex;gap:14px;align-items:flex-start}
.hours-text{color:var(--red);font-size:27px;line-height:1.2;letter-spacing:.5px}
.cost{position:absolute;left:445px;top:834px;display:flex;gap:12px;align-items:flex-start}
.cost-label{color:var(--navy);font-size:19px;margin-top:4px}
.cost-icon{width:32px;height:32px;border-radius:50%;background:var(--navy);color:var(--white);
  display:flex;align-items:center;justify-content:center;font-size:22px;margin-top:4px}
.cost-text{color:var(--navy);font-size:27px;line-height:1.2;letter-spacing:.5px}
.dash-mid{position:absolute;left:32px;top:918px;width:753px;border-top:2px dashed var(--rule)}
.hosted{position:absolute;left:43px;top:960px;width:460px;font-family:"Oswald",sans-serif;font-weight:500;
  font-size:10.5px;line-height:1.45;color:var(--ink);text-transform:uppercase;letter-spacing:.3px}
.partner{position:absolute;font-size:22px;color:var(--navy);text-align:center;line-height:1.05}
.partner-comets{left:520px;top:968px;width:130px;font-size:32px}
.partner-league{left:680px;top:950px;width:100px}
.rule-solid{position:absolute;left:32px;top:1036px;width:753px;border-top:2px solid var(--ink)}
.dash-bottom{position:absolute;left:32px;top:1050px;width:753px;border-top:2px dashed var(--rule)}
.register{position:absolute;left:58px;top:1070px;color:var(--red);font-size:32px;line-height:1.3;transform:rotate(-8deg);transform-origin:left top}
.info{position:absolute;top:1082px}
.info-head{display:flex;align-items:center;gap:10px;color:var(--navy);font-size:18px}
.info-body{margin-top:10px;margin-left:30px;color:var(--ink);font-size:21px;line-height:1.3;letter-spacing:.5px}
.info-location{left:260px}
.info-contact{left:512px}
</style>
</head>
<body>
<main class="flyer">
  <div class="hero-photo" role="img" aria-label="Photo of a young player in a batting helmet sliding head-first into base as a fielder's glove holds the ball, on a sunny dirt infield"></div>

  <svg class="grey-panel" width="817" height="820" viewBox="0 0 817 820" aria-hidden="true">
    <polygon points="0,457 455,457 455,610 817,610 817,820 0,820" fill="#ffffff"/>
    <polygon points="0,457 455,457 370,808 0,808" fill="#d0d2d5"/>
    <rect x="0" y="808" width="817" height="12" fill="#ffffff"/>
  </svg>

  <div class="logo-badge">
    <span class="logo-name">Kestrel</span>
  </div>

  <p class="softball script">softball</p>
  <h1 class="headline"><span class="summer">SUMMER</span><span class="camp">CAMP</span></h1>
  <p class="year">2017</p>
  <p class="audience script">for boys and girls</p>
  <div class="dash-top"></div>

  <p class="weeks">Weeks of<br>July 10th - 14th<br>July 17th - 21st.</p>

  <div class="ages">
    <svg width="34" height="30" viewBox="0 0 34 30" aria-hidden="true">
      <circle cx="9" cy="4" r="3.5" fill="#1f3864"/><rect x="4" y="9" width="10" height="11" rx="2" fill="#1f3864"/>
      <rect x="5" y="19" width="3" height="10" fill="#1f3864"/><rect x="10" y="19" width="3" height="10" fill="#1f3864"/>
      <circle cx="25" cy="4" r="3.5" fill="#1f3864"/><polygon points="25,8 32,22 18,22" fill="#1f3864"/>
      <rect x="21" y="21" width="3" height="8" fill="#1f3864"/><rect x="26" y="21" width="3" height="8" fill="#1f3864"/>
    </svg>
    <p class="ages-label">Players<br>Ages</p>
  </div>
  <div class="ages-circle">5 - 11</div>

  <div class="hours">
    <svg width="34" height="36" viewBox="0 0 34 36" aria-hidden="true">
      <circle cx="17" cy="20" r="13" fill="none" stroke="#d6232b" stroke-width="3.5"/>
      <rect x="13" y="1" width="8" height="4" fill="#d6232b"/>
      <line x1="17" y1="20" x2="23" y2="14" stroke="#d6232b" stroke-width="3" stroke-linecap="round"/>
    </svg>
    <p class="hours-text">Full day = 9:30am - 2:30pm<br>Half day = 9:30am - 11:30am.</p>
  </div>

  <div class="cost">
    <span class="cost-label script">Cost:</span>
    <span class="cost-icon">$</span>
    <p class="cost-text">$295 / Full day<br>$195/ Half day</p>
  </div>

  <div class="dash-mid"></div>

  <p class="hosted">Hosted by "Kestrel Baseball"<br>Affiliated with the Harbor Comets Travel Baseball &amp; Softball Club and<br>the Maple Ridge Youth League</p>

  <p class="partner partner-comets">Comets</p>
  <p class="partner partner-league">Maple Ridge Youth League</p>

  <div class="rule-solid"></div>
  <div class="dash-bottom"></div>

  <p class="register script">Register<br>today!</p>

  <div class="info info-location">
    <p class="info-head script">
      <svg width="18" height="24" viewBox="0 0 18 24" aria-hidden="true"><path d="M9 0C4 0 0 4 0 9c0 6 9 15 9 15s9-9 9-15C18 4 14 0 9 0z" fill="#1f3864"/><circle cx="9" cy="9" r="3.5" fill="#fff"/></svg>
      Camp Location:
    </p>
    <p class="info-body">Camp location MRYL,<br>Route 9C Birch Hollow.</p>
  </div>

  <div class="info info-contact">
    <p class="info-head script">
      <svg width="16" height="28" viewBox="0 0 16 28" aria-hidden="true"><rect x="3" y="0" width="2.5" height="8" fill="#1f3864"/><rect x="0" y="7" width="16" height="21" rx="3" fill="#1f3864"/><rect x="4" y="11" width="8" height="5" fill="#fff"/><circle cx="8" cy="22" r="2.5" fill="#fff"/></svg>
      Contact:
    </p>
    <p class="info-body">Phone 555-240-7813, email<br>info@kestrelball.example</p>
  </div>
</main>
</body>
</html>
```